Tampa Bay fishing guide needs stunning website.

I currently have a site - www.reelcoveguide.net which I personally put together using the Pagely platform and I am looking for a redesign on a different platform (Sitecraft?) that will allow me to easily create landing pages in the future. Would like to have a block for visitors to opt in to newsletter. Need social media links on all pages.

I would like to let my visitors know that I am able to handle their fishing charter needs here in the Tampa Bay area, if I'm not available for the dates they are looking to go I can refer them to a reputable captain in the area.

Target Market(s)

United States

Industry/Entity Type

Tourism

Coding

Coded - Design and coding required

Number of Pages Required

5+ page

Font styles to use
Sans Serif

Colors
0355a3
3176b5
85abd2
fbf289

Requirements
Must have
• Mobile Responsive, Ability to insert Vantor Metrics, Chatterbox pixels, ability to add custom landing pages in future
Nice to have
• Clean, easy navigation

```html
<!DOCTYPE html>
<html lang="en">
<head>
<meta charset="utf-8">
<title>Capt. Wade Harlan – Tampa Bay Fishing Charters</title>
<link href="https://fonts.googleapis.com/css2?family=Courgette&family=Arimo:wght@400;700&display=swap" rel="stylesheet">
<style>
:root{
  --blue-dark:#0355a3;
  --blue:#3176b5;
  --blue-light:#85abd2;
  --yellow:#fbf289;
  --ink:#555;
  --soft:#f4f8fa;
  --line:#e3eaef;
  --black:#111;
}
*{box-sizing:border-box;margin:0;padding:0}
html,body{width:1200px;height:3371px;overflow:hidden}
body{font-family:"Arimo",Arial,sans-serif;color:var(--ink);background:#fff}
.script{font-family:"Courgette",cursive}
.section-title{font-family:"Courgette",cursive;color:var(--blue-dark);font-size:38px;text-align:center;font-weight:400}

/* header */
.topbar{height:126px;position:relative}
.follow{position:absolute;left:78px;top:24px;font-size:17px;color:#555}
.socials{display:flex;gap:8px;margin-top:10px}
.socials span{width:40px;height:40px;border-radius:50%;border:1.5px solid #999;display:block}
.socials span.primary{background:var(--blue-dark);border-color:var(--blue-dark)}
.brand{position:absolute;left:0;right:0;top:30px;text-align:center;font-family:"Courgette",cursive;color:var(--blue-dark);font-size:48px}
.call{position:absolute;right:78px;top:28px;display:flex;gap:14px;align-items:center}
.call-text small{display:block;font-size:17px;color:#555}
.call-text strong{font-size:28px;color:var(--blue-dark);font-weight:400}

.nav{height:63px;background:var(--blue);display:flex;padding-left:157px}
.nav a{color:#fff;text-decoration:none;font-size:17px;line-height:63px;padding:0 28px}
.nav a.active{background:var(--blue-dark)}

.hero{height:501px;position:relative;background:linear-gradient(180deg,#8fc1e8 0%,#4d92cc 55%,#1f5f97 100%)}
.hero p{position:absolute;right:76px;top:165px;width:760px;text-align:right;font-family:"Courgette",cursive;color:#fff;font-size:33px;line-height:47px}

/* intro */
.intro{height:418px;position:relative;border-bottom:1px solid var(--line)}
.intro h1{position:absolute;left:78px;top:52px;width:660px;font-family:"Courgette",cursive;color:var(--blue-dark);font-size:37px;line-height:52px;font-weight:400}
.intro p{position:absolute;left:78px;top:170px;width:680px;font-size:14px;line-height:25px;color:#666}
.intro .fish{position:absolute;left:760px;top:63px;width:364px;height:240px;background:radial-gradient(ellipse at 45% 55%,#c9b38a 0%,#8a7a55 45%,rgba(255,255,255,0) 70%)}

/* rates */
.rates{height:741px;background:var(--soft);padding-top:58px;border-bottom:1px solid var(--line)}
.rate-grid{display:grid;grid-template-columns:repeat(3,315px);column-gap:47px;row-gap:36px;margin:40px 0 0 76px}
.rate-card{height:247px;position:relative;background:var(--black)}
.rate-card .photo{height:184px;background:linear-gradient(160deg,#6f8a7a,#2e4a44 60%,#16241f)}
.rate-card .book{position:absolute;right:-2px;top:46px;background:var(--blue);color:#fff;font-family:"Courgette",cursive;font-size:20px;padding:10px 22px}
.rate-card p{color:#fff;font-size:15px;line-height:22px;text-align:center;padding:8px 10px}

/* testimonials */
.testimonials{height:326px;position:relative;padding-top:58px;border-bottom:1px solid var(--line)}
.quote-badge{position:absolute;left:564px;top:118px}
.arrow{position:absolute;top:98px;width:42px;height:42px}
.arrow.left{left:76px}.arrow.right{right:76px}
.quote{position:absolute;left:0;right:0;top:210px;text-align:center;font-size:17px;color:#444}
.quote .mark{color:var(--blue-dark);font-size:30px;vertical-align:-6px;margin:0 6px}
.cite{position:absolute;left:0;right:0;top:250px;text-align:center;font-family:"Courgette",cursive;color:var(--blue-dark);font-size:18px}

/* pickup */
.pickup{height:425px;background:var(--soft);padding-top:52px;border-bottom:1px solid var(--line)}
.locations{display:flex;gap:14px;margin:40px 0 0 76px}
.loc{width:252px;height:218px;position:relative;background:linear-gradient(135deg,#e9eef0,#cfdde6 60%,#b9d3ea)}
.loc span{position:absolute;left:0;right:0;bottom:0;height:49px;line-height:49px;text-align:center;background:var(--blue);color:#fff;font-family:"Courgette",cursive;font-size:19px}
.loc.featured{background:var(--blue);color:#fff;text-align:center;padding-top:64px}
.loc.featured h3{font-family:"Courgette",cursive;font-weight:400;font-size:23px}
.loc.featured p{font-size:15px;line-height:22px;margin-top:10px}

/* contact */
.contact{height:456px;padding-top:62px}
.contact .lead{text-align:center;font-size:14px;line-height:24px;color:#444;margin-top:14px}
.form{position:relative;height:230px;margin-top:24px}
.field{position:absolute;left:231px;width:313px;height:45px;border:1px solid #ccc;border-radius:3px;font-size:14px;color:#999;padding:13px 12px}
.field.focus{border-color:var(--blue);color:var(--blue-dark)}
.message{position:absolute;left:551px;top:0;width:415px;height:148px;border:1px solid #ccc;border-radius:3px;font-size:14px;color:#999;padding:13px 12px}
.submit{position:absolute;left:521px;top:160px;width:158px;height:56px;background:var(--blue);color:#fff;font-family:"Courgette",cursive;font-size:20px;text-align:center;line-height:56px}

/* footer */
.footer{height:256px;background:var(--blue);border-top:5px solid var(--blue-dark);display:grid;grid-template-columns:265px 248px 286px 250px;padding:26px 0 0 78px;color:#fff}
.footer h4{font-family:"Courgette",cursive;font-weight:400;font-size:19px;margin-bottom:12px}
.footer ul{list-style:none;font-size:14px;line-height:24px}
.footer ul li::before{content:"» "}
.getintouch .row{display:flex;gap:14px;font-size:14px;line-height:21px;margin-bottom:14px;color:#e6eef7}
.newsletter p{font-size:14px;line-height:21px;color:#e6eef7}
.newsletter .email{margin-top:10px;width:250px;height:42px;background:#eee;color:#888;font-size:14px;padding:13px 12px}
.newsletter .subscribe{margin-top:10px;width:166px;height:42px;background:var(--blue-dark);font-family:"Courgette",cursive;font-size:18px;text-align:center;line-height:42px}
.cards{display:grid;grid-template-columns:repeat(2,110px);gap:8px}
.cards span{display:flex;align-items:center;gap:6px;background:#fff;color:var(--blue-dark);font-size:14px;font-weight:700;height:36px;padding:0 8px}
.cards span i{width:10px;height:10px;background:var(--blue);display:block}
.copyright{height:59px;background:var(--blue-dark);color:#dce8f4;text-align:center;font-size:14px;line-height:59px}
.copyright b{color:#fff}
</style>
</head>
<body>

<header class="topbar">
  <div class="follow">Follow Us On:
    <div class="socials">
      <span class="primary" aria-label="Chatterbox"></span>
      <span aria-label="Chirper"></span>
      <span aria-label="Plusline"></span>
    </div>
  </div>
  <div class="brand">Capt. Wade Harlan</div>
  <div class="call">
    <svg width="46" height="46" viewBox="0 0 24 24" aria-hidden="true"><path fill="#0355a3" d="M6.6 10.8a15.1 15.1 0 0 0 6.6 6.6l2.2-2.2a1 1 0 0 1 1-.25 11.4 11.4 0 0 0 3.6.57 1 1 0 0 1 1 1V20a1 1 0 0 1-1 1A17 17 0 0 1 3 4a1 1 0 0 1 1-1h3.5a1 1 0 0 1 1 1c0 1.25.2 2.45.57 3.57a1 1 0 0 1-.25 1z"/></svg>
    <div class="call-text"><small>Call Us Now</small><strong>123 555 0142</strong></div>
  </div>
</header>

<nav class="nav">
  <a class="active">HOME</a><a>ABOUT US</a><a>PICK UP LOCATION</a><a>RATES</a><a>CONTACT US</a><a>GIFT CARD</a>
</nav>

<section class="hero" role="img" aria-label="Anglers on a charter boat holding a large tarpon over open bay water, fishing rod in foreground">
  <p>Come with fishing guide, Tampa Bay fishing charter most respected Captain, 25 year Native Guide</p>
</section>

<section class="intro">
  <h1>Tampa Bay, Fishing Guid, Tampa Bay Fishing Charters</h1>
  <p>Capt. Wade Harlan, with over 20 years' experience, Native fishing charter tampa charter captain offering full and half day fishing charters on the waters of Tampa Bay. If you're looking for a great fishing charter tampa don't hesitate to contact Capt. Wade or you can simply book your trip online here. Come enjoy a wonderful day fishing charters Tampa for Tarpon, Snook, Redfish, Trout, Sharks, Cobia, Spanish mackerel as well as others aboard Capt. Wade Harlan Sport fishing Charters boat. Capt. Wade will work hard to ensure that you and your guests have a memorable day enjoying the wonderful gamefish that Tampa Bay has to offer.</p>
  <div class="fish" role="img" aria-label="Leaping gamefish"></div>
</section>

<section class="rates">
  <h2 class="section-title">Our Rates</h2>
  <div class="rate-grid">
    <div class="rate-card"><div class="photo" role="img" aria-label="Angler holding a catch on deck"></div><span class="book">Book Now !</span><p>Half Day (4 hour) Charter 1-3 people $399, 4 people $499</p></div>
    <div class="rate-card"><div class="photo" role="img" aria-label="Guests with a redfish aboard"></div><span class="book">Book Now !</span><p>3/4 Day (6 hour) Charter 1-3 people $499, 4 people $599</p></div>
    <div class="rate-card"><div class="photo" role="img" aria-label="Angler fighting a fish at the rail"></div><span class="book">Book Now !</span><p>Full Day (8 hours) Charter 1-3 people $599, 4 people $699</p></div>
    <div class="rate-card"><div class="photo" role="img" aria-label="Angler holding a catch on deck"></div><span class="book">Book Now !</span><p>Half Day (4 hour) Charter 1-3 people $399, 4 people $499</p></div>
    <div class="rate-card"><div class="photo" role="img" aria-label="Guests with a redfish aboard"></div><span class="book">Book Now !</span><p>3/4 Day (6 hour) Charter 1-3 people $499, 4 people $599</p></div>
    <div class="rate-card"><div class="photo" role="img" aria-label="Angler fighting a fish at the rail"></div><span class="book">Book Now !</span><p>Full Day (8 hours) Charter 1-3 people $599, 4 people $699</p></div>
  </div>
</section>

<section class="testimonials">
  <h2 class="section-title">Testimonials</h2>
  <svg class="arrow left" viewBox="0 0 42 42" aria-hidden="true"><circle cx="21" cy="21" r="20" fill="none" stroke="#999" stroke-width="1.5"/><path d="M24 13l-8 8 8 8" fill="none" stroke="#777" stroke-width="2"/></svg>
  <svg class="arrow right" viewBox="0 0 42 42" aria-hidden="true"><circle cx="21" cy="21" r="20" fill="none" stroke="#999" stroke-width="1.5"/><path d="M18 13l8 8-8 8" fill="none" stroke="#777" stroke-width="2"/></svg>
  <svg class="quote-badge" width="72" height="72" viewBox="0 0 72 72" aria-hidden="true"><circle cx="36" cy="36" r="34" fill="none" stroke="#0355a3" stroke-width="3"/><text x="36" y="58" text-anchor="middle" font-family="Georgia,serif" font-size="56" font-weight="700" fill="#0355a3">“</text></svg>
  <p class="quote"><span class="mark">“</span>Congratulations on winning the Bayshore Celebrity Grand Slam Tournament<span class="mark">”</span></p>
  <p class="cite">Dale Whitmore, Former Governor of Florida</p>
</section>

<section class="pickup">
  <h2 class="section-title">Pick Up Location</h2>
  <div class="locations">
    <div class="loc featured" role="img" aria-label="Map of Pelican Point Marina"><h3>Pelican Point Marina</h3><p>4210 Harbor Lane South,<br>St. Petersburg, FL 33700</p></div>
    <div class="loc" role="img" aria-label="Map of Mangrove Cove, Ruskin"><span>Mangrove Cove - Ruskin</span></div>
    <div class="loc" role="img" aria-label="Map of Causeway Boat Ramp"><span>Causeway Boat Ramp</span></div>
    <div class="loc" role="img" aria-label="Map of Kingfisher Boat Ramp"><span>Kingfisher Boat Ramp</span></div>
  </div>
</section>

<section class="contact">
  <h2 class="section-title">Contact Us</h2>
  <p class="lead">Please fell free to reach out to Capt. Wade with any questions you might have.&nbsp; Just simply fill out the form to the left<br>and he will get back with you as soon as he gets off the water.</p>
  <div class="form">
    <div class="field focus" style="top:0">Name *</div>
    <div class="field" style="top:52px">Email *</div>
    <div class="field" style="top:104px">Phone *</div>
    <div class="message">Message *</div>
    <div class="submit">Submit</div>
  </div>
</section>

<footer class="footer">
  <div>
    <h4>Sitemap</h4>
    <ul><li>Home</li><li>About Us</li><li>Pick Up Location</li><li>Rates</li><li>Contact Us</li><li>Gift Card</li></ul>
  </div>
  <div class="getintouch">
    <h4>Get In Touch</h4>
    <div class="row"><svg width="18" height="22" viewBox="0 0 18 22" aria-hidden="true"><path d="M9 1a7 7 0 0 1 7 7c0 5-7 13-7 13S2 13 2 8a7 7 0 0 1 7-7z" fill="none" stroke="#fff" stroke-width="1.5"/><circle cx="9" cy="8" r="2.5" fill="none" stroke="#fff" stroke-width="1.5"/></svg><div>Pelican Point Marina<br>Mangrove Cove - Ruskin<br>Causeway Boat Ramp<br>Kingfisher Boat Ramp</div></div>
    <div class="row"><svg width="18" height="18" viewBox="0 0 24 24" aria-hidden="true"><path fill="none" stroke="#fff" stroke-width="1.8" d="M6.6 10.8a15.1 15.1 0 0 0 6.6 6.6l2.2-2.2a1 1 0 0 1 1-.25 11.4 11.4 0 0 0 3.6.57 1 1 0 0 1 1 1V20a1 1 0 0 1-1 1A17 17 0 0 1 3 4a1 1 0 0 1 1-1h3.5a1 1 0 0 1 1 1c0 1.25.2 2.45.57 3.57a1 1 0 0 1-.25 1z"/></svg><div>813-555-0199</div></div>
    <div class="row"><svg width="18" height="14" viewBox="0 0 18 14" aria-hidden="true"><rect x="1" y="1" width="16" height="12" fill="none" stroke="#fff" stroke-width="1.5"/><path d="M1 1l8 7 8-7" fill="none" stroke="#fff" stroke-width="1.5"/></svg><div>captwade@harlanmail.com</div></div>
  </div>
  <div class="newsletter">
    <h4>Newsletter</h4>
    <p>Would you like to receive exclusive access to articles, white papers &amp; our regular monthly newsletter?</p>
    <div class="email">Enter Email Id</div>
    <div class="subscribe">Subscribe</div>
  </div>
  <div>
    <h4>We Accept</h4>
    <div class="cards">
      <span><i></i>PayWell</span><span><i></i>CardOne</span>
      <span><i></i>Vista</span><span><i></i>AmeriPay</span>
    </div>
  </div>
</footer>
<div class="copyright">©<b>Capt. Wade Harlan</b>- 2016. All Rights Reserved</div>

</body>
</html>
```